Give Gold Kite an Online Presence!

Gold Kite Property Maintenance is an Australian Owned property maintenance company who needs a stand out online presence.

GK maintains many buildings and sites and wants to appeal to a corporate professional market with their brand new website. GK is essentially a handyman service offering all maintenance services to home owners, office managers, real estate agents and strata managers.

The Website:
We need a corporate website that appeals to our broader customer base (property owners, property managers, office managers) the copy is being written by a professional so use filler text for now.

Things that we want:
Home page that sets us apart and appeals to the corporate and residential market. The home page needs to not focus on either the residential or commercial market. The home page should focus on our logo and branding. We have a logo already and it is attached to the brief, please use it and try to consider the colour pallette that goes with it. Whilst we want the site to appear strong and manly it is important to remember that 95% of our customers are female so we need the site to be appealing to women. Women need to believe that we are strong, dependable and trustworthy.
We'd like a quote page and potentially also the ability to get a quote from the home page (please don't put it in if it ruins the overall feel of the home page)
An "about us" page
A contact us page
A blog that's built in (we don't want to link to an external blog)
(overall we'd expect to have 6 or 7 pages total)

The site will also need coding - we expect this to be done in a separate project but need you to consider a few things about the coding side of things.

It needs to be iPhone and iPad compatible.

We'd like you to suggest the best CMS that you would use or if you would suggest not using a CMS please let us know with your submissions.

Target Market(s)

Property owners, office managers and property managers who need maintenance on buildings (So all of them)

Industry/Entity Type

Property Maintenance

Requirements
Must have
• Our Logo
Home page
About Us
Residential
Commercial
Real Estate/Strata
Contact Us/Quote
Blog
Nice to have
• Quote form included in home page
Movement on the home page at least
Should not have
• other logos, too much colour
NO FLASH

```html
<!DOCTYPE html>
<html lang="en">
<head>
<meta charset="utf-8">
<title>Gold Kite Property Maintenance</title>
<link rel="stylesheet" href="https://fonts.googleapis.com/css2?family=Montserrat:wght@300;700&family=Oswald:wght@500&family=Arimo:wght@400;700&family=Fira+Sans+Condensed:ital,wght@1,500&display=swap">
<style>
:root{
  --orange:#f7931e;
  --orange-deep:#f05a0a;
  --orange-light:#fbb03b;
  --ink:#1a1a1a;
  --bar-top:#3a3a3a;
  --bar-bottom:#050505;
  --text:#555;
  --heading:#5a5a5a;
  --rule:#cfcfcf;
  --white:#fff;
  --page:#f2f2f2;
}
*{margin:0;padding:0;box-sizing:border-box}
html,body{width:1200px;height:1156px;overflow:hidden;background:var(--white)}
body{font-family:"Arimo",Arial,sans-serif;color:var(--text);position:relative}
.abs{position:absolute}

/* top navigation */
.topbar{left:0;top:0;width:1200px;height:46px;background:linear-gradient(var(--bar-top),var(--bar-bottom) 70%)}
.main-nav{left:125px;top:0;height:46px;display:flex;border-left:1px solid #444}
.main-nav a{display:flex;align-items:center;justify-content:center;height:46px;border-right:1px solid #444;color:var(--white);text-decoration:none;font:500 11px "Oswald",sans-serif;letter-spacing:.2px;text-transform:uppercase}
.search{left:918px;top:10px;width:186px;height:23px;border-radius:5px;background:linear-gradient(#222,#111);border:1px solid #555;font:11px "Arimo",sans-serif;color:#888;padding:5px 0 0 124px}
.search svg{position:absolute;left:14px;top:4px}

/* hero */
.hero{left:0;top:46px;width:1200px;height:297px;overflow:hidden;background:linear-gradient(90deg,#f5a31f 0%,var(--orange) 30%,#f27a10 70%,var(--orange-deep) 100%)}
.hero-glow{left:60px;top:0;width:360px;height:297px;background:radial-gradient(circle at 50% 55%,#ffd23a 0%,rgba(255,190,40,.6) 35%,rgba(255,160,30,0) 70%)}
.skyline{left:0;bottom:0;width:1200px;height:95px;background:linear-gradient(rgba(20,15,10,0),rgba(20,15,10,.55) 40%,#120d08 80%)}
.brand{left:128px;top:190px;width:230px;text-align:center;color:var(--white);font:700 21px/22px "Montserrat",sans-serif}
.brand small{display:block;font:700 15px/18px "Montserrat",sans-serif}
.hero-title{left:464px;top:52px;color:var(--white);font:700 31px "Montserrat",sans-serif;letter-spacing:-1px}
.hero-copy{left:464px;top:118px;width:420px;color:var(--white);font:300 21.5px/29px "Montserrat",sans-serif}

/* content area */
.content-bg{left:0;top:343px;width:1200px;height:130px;background:linear-gradient(#d9d9d9,var(--white))}
.footer-fade{left:0;top:996px;width:1200px;height:50px;background:linear-gradient(var(--white),#d4d4d4)}
.section-title{font:500 italic 19px "Fira Sans Condensed",sans-serif;color:var(--heading)}
.section-title span{color:var(--orange)}
.rule{height:0;border-top:1px dotted var(--rule)}
.body-copy{font-size:11.5px;line-height:14px;color:var(--text)}
.vdivider{left:755px;top:433px;height:543px;border-left:1px dotted #bbb}

.services{left:140px;top:564px;list-style:none}
.services li{height:37px;display:flex;align-items:center;font:700 12px "Arimo",sans-serif;letter-spacing:.6px;color:#555}
.services li::before{content:"";width:11px;height:11px;border-radius:50%;background:radial-gradient(circle at 40% 35%,#ffe066,#f0a000);border:1px solid #c98500;margin-right:17px}
.services li:nth-child(3){height:38px}

.photo{background:var(--white);padding:5px;box-shadow:1px 3px 6px rgba(0,0,0,.35)}
.photo div{width:100%;height:100%}
.photo-work{left:427px;top:573px;width:124px;height:132px;transform:rotate(-6deg)}
.photo-work div{background:linear-gradient(160deg,#5a8fc0,#b9b2a0 50%,#5c7a3a)}
.photo-tower{left:548px;top:600px;width:148px;height:120px;transform:rotate(5deg)}
.photo-tower div{background:linear-gradient(135deg,#1d4f86,#7fb3de 50%,#2a5d90)}

.seal{left:118px;top:776px;width:88px;height:88px;border-radius:50%;background:radial-gradient(circle,#1d1d1d 55%,#d9a21b 57%,#f3c542 80%,#b98512)}

/* right column */
.news-title{font:700 12px "Arimo",sans-serif;letter-spacing:.6px;color:#555}
.read-more{font-size:8.5px;color:var(--orange-deep);text-decoration:underline}
.contact-info{font:700 12px/14.5px "Arimo",sans-serif;letter-spacing:.6px;color:#444}
.btn{display:flex;align-items:center;justify-content:center;height:23px;border-radius:12px;color:var(--white);font:12px "Arimo",sans-serif}
.btn-contact{left:835px;top:915px;width:59px;background:linear-gradient(#555,#111)}
.btn-quote{left:906px;top:915px;width:59px;background:linear-gradient(#ffa33a,var(--orange-deep))}

/* footer */
.footer{left:0;top:1046px;width:1200px;height:110px;background:linear-gradient(#3a3a3a,#0a0a0a);border-top:2px solid #e6e6e6}
.footer-nav{left:0;top:1080px;width:1200px;height:18px}
.footer-nav a{position:absolute;transform:translateX(-50%);color:#ddd;text-decoration:none;font:10px "Arimo",sans-serif;letter-spacing:1px;text-transform:uppercase}
.footer-sep{top:1070px;height:30px;border-left:1px solid #4a4a4a}
</style>
</head>
<body>

<header>
  <div class="abs topbar"></div>
  <nav class="abs main-nav">
    <a href="#" style="width:94px">Home</a>
    <a href="#" style="width:115px">About Us</a>
    <a href="#" style="width:125px">Residential</a>
    <a href="#" style="width:113px">Commercial</a>
    <a href="#" style="width:118px">Real Estate</a>
    <a href="#" style="width:116px">Contact Us</a>
  </nav>
  <div class="abs search">
    <svg width="16" height="16" viewBox="0 0 16 16"><circle cx="10" cy="6" r="4.5" fill="none" stroke="#ccc" stroke-width="1.6"/><line x1="6.6" y1="9.4" x2="2" y2="14" stroke="#d9a21b" stroke-width="2.4" stroke-linecap="round"/></svg>
    search...
  </div>
</header>

<section class="abs hero">
  <div class="abs hero-glow"></div>
  <div class="abs skyline" role="img" aria-label="Dark city skyline silhouette along the bottom of the banner"></div>
  <div class="abs brand" style="top:191px;left:128px">Gold Kite<small>Property Maintenance</small></div>
  <h1 class="abs hero-title">We are Gold Kite</h1>
  <p class="abs hero-copy">Our goal is to connect people in search of quality property maintenance both for residential and commercial clients.</p>
</section>

<div class="abs content-bg"></div>

<main>
  <h2 class="abs section-title" style="left:131px;top:396px">About <span>Us</span></h2>
  <div class="abs rule" style="left:131px;top:433px;width:469px"></div>
  <p class="abs body-copy" style="left:131px;top:459px;width:580px">Nemo enim ipsam voluptatem quia voluptas sit aspernatur aut odit aut fugit, sed quia consequuntur magni dolores eos qui ratione voluptatem sequi nesciunt.</p>
  <p class="abs body-copy" style="left:131px;top:501px;width:580px">Neque porro quisquam est, qui dolorem ipsum quia dolor sit amet, consectetur, adipisci velit, sed quia non numquam eius modi tempora incidunt ut labore et dolore magnam aliquam quaerat voluptatem.</p>

  <ul class="abs services">
    <li>Residential Services</li>
    <li>Commercial Services</li>
    <li>Real Estate Services</li>
    <li>Other Services</li>
    <li>Most Popular Services</li>
  </ul>

  <div class="abs photo photo-work"><div role="img" aria-label="Photo of tradesmen working on a roof, painting and fixing electrics"></div></div>
  <div class="abs photo photo-tower"><div role="img" aria-label="Photo of a glass office tower"></div></div>

  <div class="abs seal" role="img" aria-label="Quality seal"></div>
  <p class="abs body-copy" style="left:227px;top:800px;width:470px">erat indoctum, ex sed mutat animal. Vidit nominavi menandri sea ei, mea id timeam</p>
  <p class="abs body-copy" style="left:233px;top:814px;width:470px">labore omittam ex. Ad discere comprehensam qui. Odio omnis rationibus pro eu.</p>
  <p class="abs body-copy" style="left:239px;top:828px;width:470px">eu vel, et pro exerci minimum.</p>
  <p class="abs body-copy" style="left:222px;top:857px;width:480px">et has, phaedrum deseruisse voluptatibus an usu, an quaeque definitionem per. Eu his</p>
  <p class="abs body-copy" style="left:206px;top:871px;width:500px">pertinacia, ex congue consectetuer vim. Et utinam luptatum cum. Augue inimicus quo cu, ius</p>
  <p class="abs body-copy" style="left:185px;top:885px;width:500px">ulis incorrupte ea.</p>
  <p class="abs body-copy" style="left:131px;top:913px;width:580px">At nec nibh solum numquam, cu simul viris detracto sea, equidem fuisset per cu.</p>

  <div class="abs vdivider"></div>

  <aside>
    <h2 class="abs section-title" style="left:835px;top:392px">Latest <span>News</span></h2>
    <div class="abs rule" style="left:832px;top:433px;width:229px"></div>

    <h3 class="abs news-title" style="left:835px;top:464px">Lorem ipsum doloret</h3>
    <p class="abs body-copy" style="left:836px;top:492px;width:232px">Quis autem vel eum iure reprehenderit qui in ea voluptate velit esse quam nihil mole.</p>
    <a class="abs read-more" style="left:1011px;top:527px">read more</a>
    <div class="abs rule" style="left:832px;top:565px;width:229px"></div>

    <h3 class="abs news-title" style="left:837px;top:592px">Lorem ipsum doloret</h3>
    <p class="abs body-copy" style="left:838px;top:620px;width:232px">Quis autem vel eum iure reprehenderit qui in ea voluptate velit esse quam nihil mole.</p>
    <a class="abs read-more" style="left:1013px;top:656px">read more</a>

    <h2 class="abs section-title" style="left:835px;top:703px">Contact <span>Us</span></h2>
    <div class="abs rule" style="left:832px;top:745px;width:229px"></div>

    <address class="abs contact-info" style="left:837px;top:778px;font-style:normal">City Name, Australia<br>14-16 Harbour Lane<br>Central, Sydney</address>
    <p class="abs contact-info" style="left:837px;top:833px">hello@goldkite.example</p>
    <p class="abs contact-info" style="left:837px;top:861px">0800 415276<br>0800 415380</p>

    <a class="abs btn btn-contact">contact</a>
    <a class="abs btn btn-quote">quote</a>
  </aside>
</main>

<div class="abs footer-fade"></div>
<footer>
  <div class="abs footer"></div>
  <nav class="abs footer-nav">
    <a href="#" style="left:245px">About Us</a>
    <a href="#" style="left:367px">Residential</a>
    <a href="#" style="left:493px">Commercial</a>
    <a href="#" style="left:636px">Real Estate/Strata</a>
    <a href="#" style="left:804px">Contact Us/Quote</a>
    <a href="#" style="left:929px">Blog</a>
  </nav>
  <div class="abs footer-sep" style="left:305px"></div>
  <div class="abs footer-sep" style="left:429px"></div>
  <div class="abs footer-sep" style="left:552px"></div>
  <div class="abs footer-sep" style="left:719px"></div>
  <div class="abs footer-sep" style="left:882px"></div>
</footer>

</body>
</html>
```